Commercial Real Estate Corporate Site

Our company sells an ERP software to Commercial Real Estate Companies, this project is part of a marketing and sales relaunch of the company.

See attached for PDF formatted Design brief

The software is a modular system where client’s can adopt one module at a time. Our customers are corporate clients who own between 10M and 10B of real estate properties. The typical customer is from the IT or the Financial arm of the company. Our differentiation in the market is that our system is built on a no-code environment, so making changes for the client is quick. Incumbents in the market have long implementation cycles, and customization is often not possible. Competitors are Quorvel, TKB, PlotNest, Vumora.

We need a design for our site which will be implemented into Brevo Forge. **All designs must be compatible with the newest version of Brevo Forge.**

We have produced the following attached assets to use in the website design.:

1. Logo
2. Brand Guidelines
3. Content for Pages
4. Menu Structures
5. Illustrations (modules)
I can't attach them because the files are too big, so they're in this google drive instead:
https://files.examplestore.net/share/k29Xa7Lq0Pz3Rt8MwB5nYc4Hv1Jd6Fe?mode=view

The mechanic for our sales process is as follows:

1. We find on module from our application that a client is interested in. The illustrations that we’ve attached represent the individual modules (elements) of the software.
1. For instance, one of our current customers has purchased a commissions module from us which helps calculate the commission that brokers receive for buying and selling their properties.
2. We provide immense value through the module, and then keep in sales communication with the client to determine which other modules we can implement for them.
1. For instance, in the example above, the client is so happy with the commissions module that they want to start working with our leasing module as well. In the next business quarter, they also choose to add our financials module to their business systems.

### Logo

Attached

### Brand Guidelines

Attached

We are open to suggestions on the secondary colour palette.

### **Site Copy**

**We require the following pages to be created; For now, we will do one Market Page, one Product Page, and one Platform / Services Page, and we will use those as inspiration to create the other dozen Marketing Pages and 30 or so Product Pages.**

**Homepage**

Attached

**Market Page** - look at the quorvel site under the Office, Industrial, Retail (https://www.quorvel.com/products/quorvel-commercial-suite/)

**Product** - One product provided, but there will be 30 - look at the vumora page

(https://www.vumora.com/products/general-accounting)

**Platform / Services Page** - pages that tell the story of our platform and services, content to be provided - the platform will use our modules as it highlights the story of the configurability and composability of the platform. Instead of the icons that they use, we want to use our modules.

- https://www.pelbrix.com/enterprise-applications-platform
- https://www.pelbrix.com/cloud-architecture

**Team Page** - just add sample content for starters (6 Team Members to start)

**Schedule Demo Page** - the call to action for all pages

(https://go.vumora.com/schedule-demo.html)

### Menu Structure

The menu is provided as an attachment.

### Illustrations Information

A note about the illustrations - we have provided an illustrator file with the modules, and if you’d like you can arrange the in any way that you’d like to. We especially like when the modules are positioned like a periodic table of the elements.

Our existing clients are

- Torvane Coop - https://www.torvanecoop.com/real-estate/
- Dalsworth Realestate https://dalsworth.com

Our competitors are

- Quorvel - www.quorvel.com
- TKB - [www.tkbsoftware.com](https://www.tkbsoftware.com/) (we don’t like how this one looks)
- Vumora - www.vumora.com
- Plotnest - www.plotnest.com

Design inspiration

- https://lark-studio.brevosite.com/velmo
- Corporate
- Established
- Modern

### Stock Images Guidance

- https://www.drafta.net/design/QXR7Lm2TpWz/Hk9vN3c8Yd41-FbqsaZRr/edit?utm_content=QXR7Lm2TpWz&utm_campaign=designshare&utm_medium=link2&utm_source=sharebutton

Target Market(s)

Commercial Real Estate Companies - they typically own a portfolio of 50 - 5000 real estate properties and need a software to manage it all.

Coding

Coded - Design and coding required

Number of Pages Required

5+ page

Font styles to use
Other font styles liked:
• Fonts defined in brand guideline

Requirements
Must have
• Brevo Forge, Use the Elemental Design, Download ai.zip and png.zip Use Brand Guideline,
Nice to have
• Check design breif

```html
<!DOCTYPE html>
<html lang="en">
<head>
<meta charset="utf-8">
<title>Korvix — Elemental</title>
<link href="https://fonts.googleapis.com/css2?family=Audiowide&family=Poppins:wght@300;400;500&display=swap" rel="stylesheet">
<style>
:root{
  --red:#e31414;
  --red-dark:#b00d0d;
  --ink:#111111;
  --dark:#1d1d1d;
  --grey-bg:#efefef;
  --text:#333333;
  --muted:#555555;
  --white:#ffffff;
  --display:'Audiowide', sans-serif;
  --body:'Poppins', sans-serif;
}
*{margin:0;padding:0;box-sizing:border-box}
html,body{width:1200px;height:3680px;overflow:hidden}
body{position:relative;background:var(--white);font-family:var(--body);color:var(--text)}
.abs{position:absolute}
.heading{font-family:var(--display);color:var(--ink);text-transform:uppercase;font-weight:400;letter-spacing:1px}
.kicker{font-family:var(--display);color:var(--red);text-transform:uppercase;font-weight:400}
.copy{font-size:15px;line-height:27px;color:var(--text);font-weight:300}
.copy p+p{margin-top:11px}
.btn{position:absolute;display:flex;align-items:center;justify-content:center;background:var(--red);color:var(--white);font-family:var(--display);font-size:13px;text-transform:uppercase;border-radius:8px;text-decoration:none;width:150px;height:45px}
.rule{position:absolute;height:2px;background:var(--red);width:118px}

/* header / hero */
.hero-band{left:0;top:0;width:1200px;height:614px;background:linear-gradient(90deg,#151515,#262626)}
.hero-photo{left:434px;top:100px;width:766px;height:594px;background:linear-gradient(180deg,#c9c6d2 0%,#b7b8c6 45%,#8f96a8 70%,#d4d6dc 100%);box-shadow:0 10px 30px rgba(0,0,0,.35)}
.brand{display:flex;align-items:center;gap:10px;font-family:var(--display);font-size:34px;color:var(--red)}
.brand-mark{width:24px;height:24px;background:var(--red);border-radius:50%}
.nav{left:333px;top:44px;display:flex;gap:36px;font-family:var(--display);font-size:13px;color:var(--white);text-transform:uppercase}
.hero-title{left:76px;top:222px;font-size:50px;color:var(--white)}
.hero-lead{left:76px;top:296px;width:480px;font-size:25px;line-height:35px;color:var(--white);font-weight:300}

/* overview */
.overview-art{left:128px;top:775px}
.overview-title{left:616px;top:768px;font-size:40px;line-height:44px}
.overview-copy{left:616px;top:872px;width:520px}

/* about */
.about-band{left:0;top:1262px;width:1200px;height:1323px;background:var(--grey-bg)}
.about-title{left:0;top:1326px;width:1200px;text-align:center;font-size:42px}
.about-kicker{left:0;top:1388px;width:1200px;text-align:center;font-size:23px}
.enterprise-title{left:74px;top:1536px;font-size:28px}
.enterprise-copy{left:74px;top:1584px;width:520px}
.enterprise-photo{left:631px;top:1507px;width:569px;height:500px;background:linear-gradient(160deg,#0f1a3a 0%,#3b4768 50%,#b9bccb 100%);clip-path:polygon(25% 0,100% 0,100% 100%,25% 100%,0 50%)}
.modules-art{left:57px;top:2095px;width:516px;height:415px;background:linear-gradient(135deg,#2e5e60 0%,#c98b3a 45%,#3c7a47 70%,#bdbdbd 100%);clip-path:polygon(0 12%,100% 0,100% 75%,20% 100%,0 60%)}
.modules-title{left:616px;top:2120px;font-size:29px;line-height:36px}
.modules-kicker{left:616px;top:2206px;font-size:21px}
.modules-copy{left:616px;top:2246px;width:520px}

/* platform */
.platform-title{left:74px;top:2656px;font-size:42px}
.platform-kicker{left:74px;top:2718px;width:520px;font-size:23px;line-height:28px}
.platform-copy{left:74px;top:2794px;width:520px}
.platform-frame{left:814px;top:2666px;width:326px;height:369px;background:var(--ink)}
.platform-photo{left:616px;top:2683px;width:510px;height:404px;background:linear-gradient(160deg,#e4e7ee 0%,#b9c0cc 55%,#8a93a3 100%)}

/* footer */
.footer{left:0;top:3170px;width:1200px;height:510px;background:linear-gradient(90deg,#1b1b1b,#3a3a3a)}
.footer-about{left:74px;top:3345px;width:300px;font-size:13px;line-height:24px;color:var(--white);font-weight:300}
.foot-col h4{font-family:var(--display);font-weight:400;font-size:18px;color:var(--white);text-transform:uppercase;margin-bottom:18px}
.foot-col ul{list-style:none;font-size:14.5px;color:var(--white);font-weight:300}
.foot-col li{height:41.5px}
.foot-divider{left:74px;top:3603px;width:1052px;height:1px;background:#4a4a4a}
.copyright{left:74px;top:3635px;font-size:12px;color:var(--white);font-weight:300}
.social{left:958px;top:3628px;display:flex;gap:20px}
.social span{width:20px;height:20px;border:2px solid var(--white);border-radius:50%}
</style>
</head>
<body>

<!-- Header & hero -->
<div class="abs hero-band"></div>
<div class="abs hero-photo" role="img" aria-label="Flowing white curved architecture against a pale evening sky"></div>
<div class="abs brand" style="left:74px;top:26px"><span class="brand-mark"></span>Korvix</div>
<nav class="abs nav"><span>Home</span><span>Markets</span><span>Products</span><span>Platform</span><span>Services</span><span>Resources</span><span>About</span><span>Contact Us</span></nav>
<h1 class="abs heading hero-title" style="color:var(--white)">Elemental</h1>
<p class="abs hero-lead">Welcome to Korvix — an infinitely composable Enterprise Applications Platform (EAP) for real estate.</p>
<a class="btn" style="left:76px;top:465px">Schedule Demo</a>

<!-- Company overview -->
<svg class="abs overview-art" width="400" height="400" viewBox="0 0 400 400" role="img" aria-label="Three red hexagons showing tinted modern architecture">
  <polygon points="199,0 298,57 298,172 199,229 100,172 100,57" fill="#d81010"/>
  <polygon points="100,172 199,229 199,344 100,400 0,344 0,229" fill="#c50d0d"/>
  <polygon points="298,172 397,229 397,344 298,400 199,344 199,229" fill="#e31414"/>
  <polyline points="100,172 199,229 298,172" fill="none" stroke="#ffffff" stroke-width="2"/>
  <line x1="199" y1="229" x2="199" y2="344" stroke="#ffffff" stroke-width="2"/>
</svg>
<h2 class="abs heading overview-title">Company<br>Overview</h2>
<div class="rule" style="left:857px;top:811px"></div>
<div class="abs copy overview-copy">
  <p>Far beyond what’s possible with tired, legacy real estate ERP software, Korvix offers a complete industry solution, architected as flexible modules that can be assembled and configured into an infinite combination of processes and workflows.</p>
  <p>The Korvix Enterprise solution seamlessly delivers both modular software and bundled services to transform your business with less risk, greater security, and lower cost.</p>
</div>
<a class="btn" style="left:616px;top:1128px">Read More</a>

<!-- About us -->
<div class="abs about-band"></div>
<h2 class="abs heading about-title">About Us</h2>
<p class="abs kicker about-kicker">One Solution - Infinite Possibilities</p>
<div class="rule" style="left:541px;top:1435px"></div>

<h3 class="abs heading enterprise-title">Korvix Enterprise</h3>
<div class="abs copy enterprise-copy">
  <p>Korvix was born from decades of real estate enterprise software development and implementation experience — spanning hundreds of blue chip global real estate investment firms. But Korvix is unlike anything you’ve experienced before.</p>
  <p>No more multi-million-dollar disruptive implementations.<br>No more waiting for upgrades and enhancements that never come.<br>No more trailing projects and disappointing customizations.<br>No more settling for less than exactly what you want.</p>
</div>
<a class="btn" style="left:74px;top:1848px">Read More</a>
<div class="abs enterprise-photo" role="img" aria-label="Illuminated curved building at night with people walking along a lit path"></div>

<div class="abs modules-art" role="img" aria-label="Software modules arranged as a three-dimensional periodic table of elements"></div>
<h3 class="abs heading modules-title">The Modules of Korvix<br>(aka Platform?)</h3>
<p class="abs kicker modules-kicker">Simple - Secure - Scalable</p>
<div class="abs copy modules-copy">
  <p>Korvix is the real estate industry’s only infinitely composable Enterprise Applications Platform (EAP), ensuring scalability, security, auditability, and compliance. Korvix is a complete solution covering all functional areas of real estate investment, development, finance, accounting, management and operations.</p>
</div>
<a class="btn" style="left:616px;top:2412px">Read More</a>

<!-- Platform -->
<h2 class="abs heading platform-title">Platform</h2>
<div class="rule" style="left:344px;top:2679px"></div>
<p class="abs kicker platform-kicker">Stop settling for less than exactly what you want</p>
<div class="abs copy platform-copy">
  <p>Korvix combines the best of all worlds in our Enterprise Applications Platform (EAP): the simplicity and scalability of custom, no-code, software and the security and confidence of a complete, SOC 2 compliant industry solution. Our modular approach enables rapid innovation and re-invention of your business by casting off the shackles of legacy ERP technology and delivering a modern, agile solution that bridges the gaps for all of your real estate workflows.</p>
</div>
<a class="btn" style="left:74px;top:3042px">Read More</a>
<div class="abs platform-frame"></div>
<div class="abs platform-photo" role="img" aria-label="Two business people talking on a curved white staircase"></div>

<!-- Footer -->
<footer class="abs footer"></footer>
<div class="abs brand" style="left:74px;top:3262px"><span class="brand-mark"></span>Korvix</div>
<p class="abs footer-about">Korvix is the real estate industry’s modern alternative to rigid, legacy ERP systems. With decades of real estate enterprise software development and implementation expertise — spanning hundreds of blue chip global real estate investment firms — we have a proven track record of enterprise excellence.</p>
<div class="abs foot-col" style="left:403px;top:3255px">
  <h4>Quick Links</h4>
  <div style="display:flex;gap:48px">
    <ul><li>Home</li><li>Markets</li><li>Products</li><li>Platform</li><li>Services</li></ul>
    <ul><li>Resources</li><li>About</li><li>Contact us</li></ul>
  </div>
</div>
<div class="abs foot-col" style="left:674px;top:3255px">
  <h4>Products</h4>
  <ul><li>Property Management</li><li>Marketing &amp; Leasing</li><li>Accounting</li><li>Utilities</li></ul>
</div>
<div class="abs foot-col" style="left:918px;top:3255px">
  <h4>Platform</h4>
  <ul><li>Composable</li><li>Modularity</li><li>Elemental</li><li>Customizable</li><li>Workflows</li><li>Competitors Comparison</li></ul>
</div>
<div class="abs foot-divider"></div>
<p class="abs copyright">© Copyright 2024 Company Name All Rights Reserved.</p>
<div class="abs social" aria-label="Social media links"><span></span><span></span><span></span><span></span><span></span></div>

</body>
</html>
```